RevelHubQZ Business Cards

Front
Has logo with a design. Website address (www.revelhubqz-example.net)
Has slogan (discover the nightlife)
Has phone number (5182297734)
Should be bold and stands out.

Back
Has details about what we offer.

Events
Search upcoming events
Submit events
Party Image Gallery
View and download HQ party images
Sign up as a contributing event photographer and get paid!
Tickets
Sell your event tickets online for free!
Direct pay
No ticket fee

Target Market(s)

These cards will be handed out in clubs and events to patrons.

Industry/Entity Type

Business

Contact Information for Business Card

Should match or mirror our website in some sort of way. Visit the website to get ideas.

Requirements
Must have
• Must be designed for a 3x3 inch card.

```html
<!DOCTYPE html>
<html lang="en">
<head>
<meta charset="utf-8">
<title>RevelHubQZ Business Cards</title>
<link rel="stylesheet" href="https://fonts.googleapis.com/css2?family=Questrial&family=Nunito+Sans:wght@700;800&display=swap">
<style>
  :root {
    --backdrop: #e0e0de;
    --card: #262626;
    --card-edge: #2e2e2e;
    --blue: #1fa6e0;
    --pink: #e0368a;
    --white: #f4f4f4;
    --grey: #b9b9b9;
  }
  * { margin: 0; padding: 0; box-sizing: border-box; }
  html, body {
    width: 1200px; height: 659px; overflow: hidden;
    background: var(--backdrop);
    font-family: "Questrial", "Century Gothic", sans-serif;
  }
  .canvas { position: relative; width: 1200px; height: 659px; }
  .card {
    position: absolute; top: 142px; width: 375px; height: 374px;
    background: radial-gradient(ellipse at 40% 35%, var(--card-edge), var(--card) 70%);
    overflow: hidden;
  }
  .card--front { left: 201px; }
  .card--back { left: 623px; }

  .brand { position: absolute; left: 27px; top: 50px; display: flex; align-items: center; gap: 10px; }
  .brand__mark { width: 26px; height: 26px; border-radius: 50%; background: var(--blue); }
  .brand__name { font-size: 30px; color: var(--blue); line-height: 1; }
  .brand__slogan {
    position: absolute; left: 27px; top: 86px; width: 320px;
    font-size: 10px; letter-spacing: 4.6px; color: var(--grey); text-transform: lowercase;
  }

  .contact { position: absolute; left: 27px; top: 199px; color: var(--white); }
  .contact__name { font-family: "Nunito Sans", sans-serif; font-weight: 800; font-size: 19px; line-height: 1.2; }
  .contact__role { font-size: 12px; color: var(--grey); margin-top: 2px; }
  .contact__lines { margin-top: 20px; font-size: 14px; line-height: 18px; }
  .contact__web-accent { color: var(--blue); }
  .contact__web-accent--pink { color: var(--pink); }

  .offer { position: absolute; left: 0; right: 0; top: 44px; text-align: center; color: var(--white); }
  .offer__title {
    font-family: "Nunito Sans", sans-serif; font-weight: 800;
    font-size: 16px; color: var(--pink); letter-spacing: 0.5px; margin-bottom: 18px;
  }
  .offer__list { list-style: none; font-size: 14px; line-height: 21.6px; }

  .level-band {
    position: absolute; left: 0; right: 0; bottom: 0; height: 32px;
    background: linear-gradient(to bottom, var(--pink) 0%, var(--pink) 45%, var(--blue) 50%, var(--blue) 100%);
    opacity: 0.9;
  }
</style>
</head>
<body>
<main class="canvas">
  <section class="card card--front">
    <div class="brand">
      <span class="brand__mark"></span>
      <span class="brand__name">RevelHubQZ</span>
    </div>
    <p class="brand__slogan">discover the nightlife</p>

    <div class="contact">
      <h1 class="contact__name">Dana Whitlow</h1>
      <p class="contact__role">Managing Director</p>
      <p class="contact__lines">
        5182297734<br>
        hello@revelhubqz-example.net<br>
        www.<span class="contact__web-accent">revelhub</span><span class="contact__web-accent--pink">qz</span>-example.net
      </p>
    </div>

    <div class="level-band" role="img" aria-label="Pink and blue equalizer level bars along the bottom edge"></div>
  </section>

  <section class="card card--back">
    <div class="offer">
      <h2 class="offer__title">WE OFFER</h2>
      <ul class="offer__list">
        <li>Events</li>
        <li>Search upcoming events</li>
        <li>Submit events</li>
        <li>Party Image Gallery</li>
        <li>View and download HQ party images</li>
        <li>Sign up as a contributing event</li>
        <li>photographer and get paid!</li>
        <li>Tickets</li>
        <li>Sell your event tickets online for free!</li>
        <li>Direct pay</li>
        <li>No ticket fee</li>
      </ul>
    </div>

    <div class="level-band" role="img" aria-label="Pink and blue equalizer level bars along the bottom edge"></div>
  </section>
</main>
</body>
</html>
```